Birchline Septic Solutions

Would like to see some single sided ones but would also like to see some double sided with one sided only being the logo. Owners name is Colin Vandro. Phone number is 555-214-0387
Services are pumping, inspections, installs, and repairs

Contact Information for Business Card

555-241-0387 Colin Vandro Maplewood, OH

```html
<!DOCTYPE html>
<html lang="en">
<head>
<meta charset="utf-8">
<title>Birchline Septic Solutions – Business Card</title>
<link href="https://fonts.googleapis.com/css2?family=Montserrat:wght@400;500;700;800&display=swap" rel="stylesheet">
<style>
  :root {
    --backdrop: #2a2623;
    --card: #1b1b1b;
    --teal: #2bbcb8;
    --white: #ffffff;
  }
  * { margin: 0; padding: 0; box-sizing: border-box; }
  html, body {
    width: 1200px; height: 842px; overflow: hidden;
    background: var(--backdrop);
    font-family: "Montserrat", sans-serif;
  }
  .sheet {
    width: 1200px; height: 842px;
    display: flex; align-items: center; justify-content: center; gap: 40px;
  }
  .card {
    position: relative;
    width: 540px; height: 309px;
    background: var(--card);
    overflow: hidden;
    box-shadow: 0 12px 30px rgba(0,0,0,.45);
  }

  /* Contact side */
  .band { position: absolute; left: 0; width: 100%; background: var(--teal); }
  .band--top { top: 4px; height: 9px; }
  .band--bottom { bottom: 8px; height: 11px; }
  .contact {
    position: absolute; top: 62px; left: 0; width: 100%;
    display: flex; flex-direction: column; align-items: center;
    color: var(--white);
  }
  .contact__name {
    color: var(--teal); font-weight: 700; font-size: 20px; letter-spacing: .04em;
    text-transform: uppercase;
  }
  .contact__rule { width: 54px; height: 1.5px; background: var(--teal); margin: 12px 0 13px; }
  .contact__line { font-size: 14px; font-weight: 500; letter-spacing: .05em; }
  .services {
    position: absolute; left: 0; width: 100%; bottom: 44px;
    display: flex; justify-content: center; align-items: center; gap: 9px;
    color: var(--white); font-size: 13.5px; font-weight: 500; letter-spacing: .05em;
    text-transform: uppercase;
  }
  .services__mark { width: 12px; height: 9px; }

  /* Logo side */
  .accent { position: absolute; width: 46px; height: 110px; }
  .accent--left { left: 0; top: 150px; }
  .accent--right { right: 0; top: 50px; }
  .brand {
    position: absolute; inset: 0;
    display: flex; flex-direction: column; align-items: center; justify-content: center;
    color: var(--white); font-weight: 800; text-transform: uppercase;
  }
  .brand__name { font-size: 52px; letter-spacing: .02em; line-height: 1; }
  .brand__tag { font-size: 17px; letter-spacing: .32em; margin-top: 10px; }
</style>
</head>
<body>
<main class="sheet">
  <section class="card card--contact">
    <div class="band band--top"></div>
    <div class="contact">
      <h1 class="contact__name">Colin Vandro</h1>
      <div class="contact__rule"></div>
      <p class="contact__line">555-214-0387</p>
      <div class="contact__rule"></div>
      <p class="contact__line">Maplewood, OH</p>
      <div class="contact__rule"></div>
    </div>
    <ul class="services">
      <li>Pumping</li>
      <li><svg class="services__mark" viewBox="0 0 12 9"><polygon points="3,0 12,0 9,9 0,9" fill="#2bbcb8"/></svg></li>
      <li>Inspections</li>
      <li><svg class="services__mark" viewBox="0 0 12 9"><polygon points="3,0 12,0 9,9 0,9" fill="#2bbcb8"/></svg></li>
      <li>Installs</li>
      <li><svg class="services__mark" viewBox="0 0 12 9"><polygon points="3,0 12,0 9,9 0,9" fill="#2bbcb8"/></svg></li>
      <li>Repairs</li>
    </ul>
    <div class="band band--bottom"></div>
  </section>

  <section class="card card--brand">
    <svg class="accent accent--left" viewBox="0 0 46 110">
      <rect x="0" y="0" width="28" height="110" fill="#2bbcb8"/>
      <rect x="36" y="0" width="4" height="110" fill="#ffffff"/>
    </svg>
    <div class="brand">
      <p class="brand__name">Birchline</p>
      <p class="brand__tag">Septic Solutions</p>
    </div>
    <svg class="accent accent--right" viewBox="0 0 46 110">
      <rect x="6" y="0" width="4" height="110" fill="#ffffff"/>
      <rect x="18" y="0" width="28" height="110" fill="#2bbcb8"/>
    </svg>
  </section>
</main>
</body>
</html>
```